Carwash Signage

We own and operate a 25m tunnel car wash in the uk. We are looking to upgrade our signage to include the following:-

Wash selection Board Size-1300x1300mm
Conditions 1300x1300mm
Instructions 1300x1300mm
Banner 2600x600mm
Stamp card flyer a5 double sided - 9 squares for stamping 3rd square needs to say free air freshener 9th square needs to say free vip car wash.

I have attached some notes for the details that are required to be included.

We are looking for a modern smart look more European car wash style than American car wash style. It should be bold and clear. with yellow/orange & blue/green,grey colours

The final design must be in a industry standard printable format.

UPDATED BRIEF AS DISCUSSED: We require design for 2 x window decals, flag design and 50% off voucher. Attached are rough layout drawings of what they should look like - we expect the designs to be in keeping with the previous designs colours, etc that have been carried out. We Look forward to hearing from you.

Target Market(s)

local car owners within a 15-20 mile radius

Colors
0054AA
0677BA
7BADD7
CADEEF
E8F1F8
0094D4
00A9DD
6FCCEA
C7EBF8
E9F6FB
00AB8E
00BBA5
67D7C9
C6EFE9
E9F9F6

Requirements
Must have
• must be sharp and modern European look

```html
<!DOCTYPE html>
<html lang="en">
<head>
<meta charset="utf-8">
<title>Coastline Car Wash – Signage Set</title>
<link rel="stylesheet" href="https://fonts.googleapis.com/css2?family=Anton&family=Oswald:wght@700&family=Russo+One&family=Outfit:wght@400;600&display=swap">
<style>
  :root{
    --canvas:#a7a7a7;
    --navy:#0b1d5c;
    --sea:#0a6d8e;
    --teal:#14c4b0;
    --white:#ffffff;
    --heart:#e3232a;
    --foam-a:#e9f6fb;
    --foam-b:#6fa9cf;
  }
  *{box-sizing:border-box;margin:0;padding:0}
  html,body{width:1200px;height:1200px;overflow:hidden;background:var(--canvas)}
  body{position:relative;font-family:"Outfit",sans-serif}

  .panel{position:absolute;overflow:hidden;color:var(--white);
    background:linear-gradient(180deg,var(--navy) 0%,var(--navy) 45%,var(--sea) 100%)}
  .card{border-radius:16px}

  .brand{position:absolute;display:flex;align-items:center;gap:8px;
    font-family:"Russo One",sans-serif;font-size:20px;letter-spacing:1px;color:var(--white);white-space:nowrap}
  .brand-dot{width:14px;height:14px;border-radius:50%;background:var(--white)}

  /* voucher front */
  .voucher{left:139px;top:118px;width:437px;height:282px;background:linear-gradient(180deg,var(--navy),#0d4f8c)}
  .voucher .brand{left:50%;top:34px;transform:translateX(-50%)}
  .offer-frame{position:absolute;left:58px;top:100px;width:344px;height:100px;border:2px solid var(--teal);
    border-radius:8px;transform:skewX(-6deg)}
  .offer{position:absolute;left:0;right:0;top:96px;text-align:center;font-family:"Oswald",sans-serif;
    font-size:86px;line-height:1;letter-spacing:1px;font-style:italic}
  .offer .pct{color:var(--teal)}
  .foam{position:absolute;left:0;right:0;bottom:0;height:95px;
    background:radial-gradient(ellipse at 30% 80%,var(--foam-a) 0%,#c7e3f2 45%,rgba(111,169,207,0) 100%),
               linear-gradient(180deg,rgba(202,222,239,0) 0%,var(--foam-a) 70%)}
  .vip{position:absolute;left:0;right:0;bottom:24px;text-align:center;font-family:"Russo One",sans-serif;
    font-style:italic;font-size:34px;letter-spacing:3px;color:var(--white);transform:skewX(-14deg)}
  .vip span{color:var(--teal)}

  /* voucher back */
  .voucher-back{left:623px;top:118px;width:436px;height:282px;background:var(--navy)}
  .voucher-back .brand{left:50%;top:30px;transform:translateX(-50%)}
  .form{position:absolute;left:23px;top:85px;width:392px}
  .row{display:flex;align-items:center;height:29px;margin-bottom:6.5px}
  .label{width:137px;height:100%;background:var(--teal);color:var(--navy);border-radius:3px;
    font-size:17px;padding-left:8px;display:flex;align-items:center}
  .colon{width:17px;text-align:center;font-size:15px}
  .field{flex:1;height:100%;background:var(--white);border-radius:4px}
  .validity{position:absolute;left:0;right:0;top:247px;text-align:center;font-size:14px;letter-spacing:.2px}

  /* tall window decal */
  .decal{left:139px;top:468px;width:307px;height:612px}
  .big-we{position:absolute;left:30px;top:30px;font-family:"Anton",sans-serif;font-size:178px;line-height:1;
    color:var(--teal);letter-spacing:4px}
  .big-love{position:absolute;left:30px;top:220px;display:flex;align-items:center;font-family:"Anton",sans-serif;
    font-size:112px;line-height:1;color:var(--teal)}
  .heart{display:block}
  .dirty{position:absolute;left:32px;top:340px;font-family:"Russo One",sans-serif;font-size:66px;line-height:1.12;
    color:var(--white);letter-spacing:1px;font-style:italic}
  .decal .rule{position:absolute;left:22px;top:515px}
  .decal .brand{left:50%;top:563px;transform:translateX(-50%)}

  /* banners */
  .banner{left:504px;width:555px;height:277px}
  .banner-a{top:468px}
  .banner-b{top:804px}
  .attended{position:absolute;left:32px;top:40px;font-family:"Russo One",sans-serif;font-style:italic;
    font-size:30px;color:var(--teal);letter-spacing:2px}
  .banner-a .brand{right:34px;top:42px;font-size:18px}
  .carwash{position:absolute;left:30px;top:80px;font-family:"Russo One",sans-serif;font-size:80px;line-height:1;
    letter-spacing:2px;font-style:italic}
  .banner .rule{position:absolute;left:38px;top:170px;width:480px;height:2px;background:linear-gradient(90deg,rgba(255,255,255,.2),#fff,rgba(255,255,255,.2))}
  .chevrons{position:absolute;left:30px;top:190px}
  .banner-b .brand{left:50%;top:30px;transform:translateX(-50%)}
  .slogan{position:absolute;left:30px;top:80px;display:flex;align-items:center;gap:14px}
  .slogan-main{display:flex;align-items:center;font-family:"Anton",sans-serif;font-size:84px;line-height:1;color:var(--teal);letter-spacing:1px}
  .slogan-side{font-family:"Russo One",sans-serif;font-style:italic;font-size:36px;line-height:1.05;color:var(--white)}
</style>
</head>
<body>

<section class="panel card voucher">
  <div class="brand"><span class="brand-dot"></span>COASTLINE CAR WASH</div>
  <div class="offer-frame"></div>
  <div class="offer"><span class="pct">50%</span> OFF</div>
  <div class="foam" role="img" aria-label="Soap foam and bubbles"></div>
  <div class="vip"><span>VIP</span> WASH</div>
</section>

<section class="panel card voucher-back">
  <div class="brand"><span class="brand-dot"></span>COASTLINE CAR WASH</div>
  <div class="form">
    <div class="row"><div class="label">Vehicle Reg</div><div class="colon">:</div><div class="field"></div></div>
    <div class="row"><div class="label">Operator</div><div class="colon">:</div><div class="field"></div></div>
    <div class="row"><div class="label">Reason</div><div class="colon">:</div><div class="field"></div></div>
    <div class="row"><div class="label">Date</div><div class="colon">:</div><div class="field"></div></div>
  </div>
  <p class="validity">VALID FOR 10 DAYS FROM ABOVE DATE</p>
</section>

<section class="panel decal">
  <div class="big-we">WE</div>
  <div class="big-love">L<svg class="heart" width="84" height="84" viewBox="0 0 100 100"><path d="M50 92 L10 50 A22 22 0 0 1 50 18 A22 22 0 0 1 90 50 Z" fill="#e3232a"/></svg>VE</div>
  <div class="dirty">DIRTY<br>CARS</div>
  <svg class="rule" width="260" height="26" viewBox="0 0 260 26"><path d="M0 24 H130 Q140 24 146 14 Q152 4 162 4 H240" stroke="#fff" stroke-width="2" fill="none"/></svg>
  <div class="brand"><span class="brand-dot"></span>COASTLINE CAR WASH</div>
</section>

<section class="panel banner banner-a">
  <div class="attended">ATTENDED</div>
  <div class="brand"><span class="brand-dot"></span>COASTLINE CAR WASH</div>
  <div class="carwash">CARWASH</div>
  <div class="rule"></div>
  <svg class="chevrons" width="500" height="72" viewBox="0 0 500 72">
    <g id="chev-row">
      <polygon points="28,0 58,0 30,36 58,72 28,72 0,36" fill="#fff"/>
      <polygon points="83,0 113,0 85,36 113,72 83,72 55,36" fill="#14c4b0"/>
      <polygon points="138,0 168,0 140,36 168,72 138,72 110,36" fill="#fff"/>
      <polygon points="193,0 223,0 195,36 223,72 193,72 165,36" fill="#14c4b0"/>
      <polygon points="248,0 278,0 250,36 278,72 248,72 220,36" fill="#fff"/>
      <polygon points="303,0 333,0 305,36 333,72 303,72 275,36" fill="#14c4b0"/>
      <polygon points="358,0 388,0 360,36 388,72 358,72 330,36" fill="#fff"/>
      <polygon points="413,0 443,0 415,36 443,72 413,72 385,36" fill="#14c4b0"/>
      <polygon points="468,0 498,0 470,36 498,72 468,72 440,36" fill="#fff"/>
    </g>
  </svg>
</section>

<section class="panel banner banner-b">
  <div class="brand"><span class="brand-dot"></span>COASTLINE CAR WASH</div>
  <div class="slogan">
    <div class="slogan-main">WE&nbsp;L<svg class="heart" width="66" height="66" viewBox="0 0 100 100"><path d="M50 92 L10 50 A22 22 0 0 1 50 18 A22 22 0 0 1 90 50 Z" fill="#e3232a"/></svg>VE</div>
    <div class="slogan-side">DIRTY<br>CARS</div>
  </div>
  <div class="rule"></div>
  <svg class="chevrons" width="500" height="72" viewBox="0 0 500 72">
    <polygon points="28,0 58,0 30,36 58,72 28,72 0,36" fill="#fff"/>
    <polygon points="83,0 113,0 85,36 113,72 83,72 55,36" fill="#14c4b0"/>
    <polygon points="138,0 168,0 140,36 168,72 138,72 110,36" fill="#fff"/>
    <polygon points="193,0 223,0 195,36 223,72 193,72 165,36" fill="#14c4b0"/>
    <polygon points="248,0 278,0 250,36 278,72 248,72 220,36" fill="#fff"/>
    <polygon points="303,0 333,0 305,36 333,72 303,72 275,36" fill="#14c4b0"/>
    <polygon points="358,0 388,0 360,36 388,72 358,72 330,36" fill="#fff"/>
    <polygon points="413,0 443,0 415,36 443,72 413,72 385,36" fill="#14c4b0"/>
    <polygon points="468,0 498,0 470,36 498,72 468,72 440,36" fill="#fff"/>
  </svg>
</section>

</body>
</html>
```